Keystonery Billboard - Financial Services Company (Investments, Tax Planning and Insurance)

Our new office has a billboard directly above the office building. We'd like something eye-catching with a strong Call to Action, with the main part of the billboard being under 7 words if possible. We'd like you to include a way to get ahold of us (either our website keystoneryllc.example or our phone number 302-418-2907. You may also include in small font something to indicate that we've been serving the area since 1980 (the DE area, the tri-state area, the Marlowe Hollow, etc.)

We offer financial planning, tax planning, and insurance, and we help our clients to focus on their goals and happiness by providing everything they need for lifelong wealth under one roof.

Our logos are attached, we use a triangle logo with green and gray. We use the tagline "discover lasting prosperity" but this does not need to be included.

Potential ideas we have seen from other financial companies-
- the concept that the driver spends more time looking at billboards than planning for their retirement
-something along the lines of "everything you need for your finances is in this building right here" planning, investments, taxes, insurance"
-don't spend your time worrying about retirement, let us help you plan for it
-are you working for your money, or is it working for you?
- retirement takes planning, we're here to help
- ready to retire? talk to us
- need investment advice?
- need help investing?
- crossing your fingers isn't a retirement plan. we can help.
- retiring soon? you need help.

Those are just general ideas, please feel free to be creative.

brand colors:
#00b585
#00b185
#000000
#ffffff
#6d6f75
#6d6f75
#6f7074
#021712
#052e24

```html
<!DOCTYPE html>
<html lang="en">
<head>
<meta charset="utf-8">
<title>Keystonery Billboard</title>
<link rel="stylesheet" href="https://fonts.googleapis.com/css2?family=Montserrat:wght@500;700;800&display=swap">
<style>
  :root {
    --brand-green: #00a55a;
    --brand-gray: #6d6f75;
    --ink-white: #ffffff;
    --page-bg: #e9ecee;
    --board-light: #fbfdfb;
    --board-mint: #d6efe8;
    --photo-green: #12a35c;
    --photo-green-deep: #0b8a4c;
    --photo-mint: #bfe7dc;
  }
  * { box-sizing: border-box; margin: 0; padding: 0; }
  html, body {
    width: 1200px;
    height: 900px;
    overflow: hidden;
    background: var(--page-bg);
    font-family: "Montserrat", Arial, sans-serif;
  }
  .billboard {
    position: absolute;
    left: 30px;
    top: 201px;
    width: 1140px;
    height: 498px;
    overflow: hidden;
    background: linear-gradient(100deg, var(--board-light) 0%, #eef8f4 45%, var(--board-mint) 100%);
  }
  .brand {
    position: absolute;
    left: 224px;
    top: 58px;
  }
  .brand-name {
    display: block;
    font-weight: 700;
    font-size: 62px;
    line-height: 1;
    letter-spacing: -1px;
    color: var(--brand-green);
  }
  .brand-tagline {
    display: block;
    margin-top: 8px;
    font-weight: 500;
    font-size: 12px;
    letter-spacing: 5px;
    text-transform: uppercase;
    color: var(--brand-gray);
  }
  .headline {
    position: absolute;
    left: 48px;
    top: 178px;
    font-weight: 800;
    font-size: 58px;
    line-height: 62px;
    letter-spacing: -0.5px;
    text-transform: uppercase;
    color: var(--brand-gray);
  }
  .headline .accent { color: var(--brand-green); }
  .cta-bar {
    position: absolute;
    left: 0;
    top: 410px;
    width: 670px;
    height: 88px;
    background: var(--brand-gray);
    clip-path: polygon(0 0, 100% 0, 94% 100%, 0 100%);
    display: flex;
    align-items: center;
    padding-left: 48px;
    color: var(--ink-white);
  }
  .cta-label {
    font-weight: 800;
    font-size: 32px;
    letter-spacing: 1px;
    margin-right: 30px;
  }
  .cta-icon {
    width: 42px;
    height: 42px;
    margin-right: 10px;
  }
  .cta-phone {
    font-weight: 700;
    font-size: 38px;
    letter-spacing: -0.5px;
  }
  .hero-photo {
    position: absolute;
    left: 666px;
    top: 0;
    width: 474px;
    height: 498px;
    clip-path: polygon(46% 0, 100% 0, 100% 100%, 0 100%);
    background: linear-gradient(170deg, var(--photo-mint) 0%, var(--photo-green) 30%, var(--photo-green-deep) 100%);
  }
</style>
</head>
<body>
  <main class="billboard">
    <div class="brand">
      <span class="brand-name">Keystonery</span>
      <span class="brand-tagline">Discover lasting prosperity</span>
    </div>

    <h1 class="headline">
      Worrying about<br>
      your <span class="accent">money?</span><br>
      <span class="accent">Us too!</span>
    </h1>

    <div class="cta-bar">
      <span class="cta-label">CALL US</span>
      <svg class="cta-icon" viewBox="0 0 42 42" aria-hidden="true">
        <circle cx="21" cy="21" r="20" fill="#ffffff"/>
        <path d="M14 11c1-1 2.5-1 3.3 0l2.6 3.4c.7 1 .6 2.3-.3 3.1l-1.6 1.4c1.2 2.6 3.2 4.6 5.8 5.8l1.4-1.6c.8-.9 2.1-1 3.1-.3l3.4 2.6c1 .8 1 2.3 0 3.3l-1.8 1.8c-1.3 1.3-3.3 1.7-5 .9-6.2-2.8-10.6-7.2-13.4-13.4-.8-1.7-.4-3.7.9-5z" fill="#6d6f75"/>
      </svg>
      <span class="cta-phone">302-418-2907</span>
    </div>

    <div class="hero-photo" role="img" aria-label="Photo of a surprised man in a dark red shirt holding a fan of dollar bills, hand on his head"></div>
  </main>
</body>
</html>
```